WP website design for Kemble

We need a wordpress design that will incorporate a professional color scheme with company logo in a clean layout. The design needs to consider that this will be developed on a responsive theme. Colors are will be the green of the logo and any others that will creatively highlight it.

Industry/Entity Type

It Company

Font styles to use
Sans Serif

Requirements
Must have
• Navigation: 1) Home 2) Auctions 3) Auction Services 4) Sellers 5) TR Kemble Livestock 6) About Us 7) Contact Us
Site will have slideshow element, image attached.
Widgets will be: 1)Email Signup form 2) Featured Auctions widget 3) Social Media (FB, Youtube, RSS) 4) News & Events blog
Footer will have smaller company logo, association logos (attached) and contact info (below)
▪ T.R. Kemble Inc. / Auctioneers
▪ 4710 NC Hwy 91
▪ Cedar Bend, NC 27999
▪ Office: (555) 318-6402
▪ Cell: (555) 274-8813
▪ email: trkemble@trkemble-example.com
Nice to have
• Site will have drop-down menus - please indicate the styling, for instance the dropdown menus

```html
<!DOCTYPE html>
<html lang="en">
<head>
<meta charset="utf-8">
<title>T.R. Kemble Inc. / Auctioneers</title>
<link href="https://fonts.googleapis.com/css2?family=Open+Sans:ital,wght@0,400;0,600;1,400&family=Cormorant+Garamond:ital,wght@1,500&display=swap" rel="stylesheet">
<style>
:root{
  --green:#3a8a1c;
  --green-dark:#2f7414;
  --green-deep:#276610;
  --green-text:#4f9a2e;
  --charcoal:#2a2a2a;
  --charcoal-2:#252525;
  --grey:#7a7a7a;
  --white:#fff;
  --ink:#333;
}
*{box-sizing:border-box;margin:0;padding:0}
html,body{width:909px;height:1200px;overflow:hidden}
body{font-family:"Open Sans",Arial,sans-serif;background:var(--white);color:var(--ink)}
.wrap{width:648px;margin:0 auto;position:relative}

.site-header{height:77px}
.brand{position:absolute;left:0;top:22px;display:flex;align-items:center;gap:5px}
.brand-mark{width:14px;height:14px;border-radius:50%;background:var(--green);flex:none}
.brand-name{font-size:9.5px;font-weight:600;color:var(--green);line-height:1.3;white-space:nowrap}
.tagline{position:absolute;left:111px;top:26px;font-family:"Cormorant Garamond",Georgia,serif;font-style:italic;font-weight:500;font-size:19px;color:var(--green);white-space:nowrap}
.call{position:absolute;right:0;top:20px;display:flex;align-items:center;gap:8px}
.call-icon{width:36px;height:36px;border-radius:50%;background:#cfcfcf;display:flex;align-items:center;justify-content:center}
.call small{display:block;font-size:8.5px;color:var(--grey);letter-spacing:.5px}
.call strong{font-size:13px;font-weight:600;color:var(--green)}

.main-nav{height:33px;background:linear-gradient(var(--green),var(--green-dark))}
.main-nav ul{list-style:none;display:flex;height:33px;border-left:1px solid var(--green-deep)}
.main-nav li{font-size:8px;font-weight:600;color:var(--white);white-space:nowrap;display:flex;align-items:center;justify-content:center;border-right:1px solid var(--green-deep)}
.n-home{width:69px}.n-auc{width:81px}.n-svc{width:117px}.n-sel{width:73px}.n-live{width:129px}.n-about{width:81px}.n-contact{width:94px}

.hero{height:342px;background:linear-gradient(#8c8c8c,#bdbdbd 45%,#777 100%);position:relative}
.slide-frame{position:absolute;left:130px;top:27px;width:649px;height:272px;background:var(--white);padding:6px}
.slide-photo{width:100%;height:100%;background:linear-gradient(#9cc6e6 0%,#c7dcea 28%,#8a7a45 45%,#c69a4a 60%,#a87a3a 75%,#6f7f8f 100%)}
.slide-caption{position:absolute;left:119px;top:197px;width:320px;height:81px;background:var(--green);clip-path:polygon(0 0,93% 0,100% 100%,0 100%);color:var(--white);padding:13px 0 0 33px}
.slide-caption h2{font-size:13.5px;font-weight:400;line-height:1.4}
.slide-caption p{font-size:12.5px;margin-top:2px}
.slide-arrows{position:absolute;left:727px;top:268px;display:flex;gap:2px}
.slide-arrows span{width:17px;height:17px;background:rgba(80,80,80,.55);color:#ddd;font-size:10px;display:flex;align-items:center;justify-content:center}

.welcome{height:150px;background:var(--charcoal);text-align:center;padding-top:34px}
.welcome h1{font-size:19px;font-weight:400;color:var(--white);margin-bottom:9px}
.welcome p{font-size:7.2px;line-height:18.5px;width:560px;margin:0 auto;font-family:Arial,sans-serif;color:#dcdcdc}

.featured{height:214px;background:var(--charcoal-2);padding-top:21px}
.section-head{display:flex;justify-content:space-between;align-items:center}
.featured h2{font-size:13px;font-weight:400;color:var(--white)}
.pager{color:#888;font-size:9px;letter-spacing:6px}
.auction-list{display:flex;gap:25px;margin-top:18px}
.auction-card{width:143px}
.auction-thumb{height:90px;border:3px solid #1c1c1c;outline:1px solid #3a3a3a}
.t1{background:linear-gradient(#a33e22,#e0a360 50%,#4a4a1a)}
.t2{background:linear-gradient(#c6d9a8,#6a9c3c 40%,#4f7d2a)}
.t3{background:linear-gradient(#cfe0ee,#5f9a3a 50%,#3b6a20)}
.t4{background:linear-gradient(#a9c8e4,#d9b36a 45%,#c08a3a)}
.auction-card h3{font-size:8.5px;font-weight:400;color:var(--green-text);margin-top:15px}
.auction-card p{font-size:6.8px;color:var(--white);margin-top:5px;padding-left:1px}

.news{height:176px;padding-top:26px}
.news h2{font-size:13px;font-weight:400;color:var(--green)}
.pager-box{display:flex;gap:1px}
.pager-box span{width:13px;height:13px;background:#bbb;color:#fff;font-size:8px;display:flex;align-items:center;justify-content:center}
.news-list{display:flex;gap:16px;margin-top:16px}
.news-item{display:flex;gap:19px;width:316px}
.news-thumb{width:116px;height:82px;flex:none}
.n1{background:linear-gradient(#1d2a4a,#8a6a3a 55%,#3a2a1a)}
.n2{background:linear-gradient(#c98a1a,#f0c040 50%,#2a1a05)}
.news-item h3{font-size:8.5px;font-weight:400;color:var(--green);margin-top:1px}
.news-item em{display:block;font-size:7px;color:#444;margin:7px 0 8px}
.news-item p{font-size:6.8px;line-height:15px;color:#555;font-family:Arial,sans-serif}

.site-footer{height:158px;background:var(--green);color:var(--white)}
.footer-cols{display:flex;padding-top:34px}
.footer-brand{width:123px;display:flex;align-items:flex-start;gap:5px;padding-top:6px}
.footer-brand .brand-mark{background:var(--white)}
.footer-brand .brand-name{color:var(--white)}
.site-footer h4{font-size:10.5px;font-weight:400;margin-bottom:9px}
.signup{width:214px}
.signup p{font-size:7px;font-family:Arial,sans-serif}
.signup .field{width:167px;height:21px;background:var(--white);border-radius:2px;margin-top:9px;font-size:7px;color:#666;padding:6px 10px;font-family:Arial,sans-serif}
.signup .btn{display:inline-block;margin-top:9px;background:#222;border-radius:2px;font-size:7px;padding:6px 12px}
.contact{width:215px;font-size:7px;line-height:17px;font-family:Arial,sans-serif;white-space:nowrap}
.contact .co{font-size:7.5px;letter-spacing:.3px;font-family:"Open Sans",Arial,sans-serif}
.follow ul{list-style:none}
.follow li{display:flex;align-items:center;gap:5px;font-size:7.5px;margin-bottom:8px;font-family:Arial,sans-serif}
.follow .dot{width:20px;height:20px;border-radius:50%;background:var(--white)}

.bottom-bar{height:50px;background:var(--green-deep);color:var(--white)}
.bottom-bar .wrap{padding-top:11px}
.foot-nav{font-size:7.5px;font-family:Arial,sans-serif}
.foot-nav span{margin:0 11px}
.copy{font-size:7px;margin-top:9px;font-family:Arial,sans-serif}
.badges{position:absolute;right:0;top:8px;display:flex;gap:10px;align-items:center}
.badges i{display:block;background:rgba(255,255,255,.85)}
.b1{width:68px;height:22px;border-radius:3px}
.b2{width:34px;height:34px;border-radius:50%}
.b3{width:36px;height:28px;border-radius:4px}
</style>
</head>
<body>

<header class="site-header">
  <div class="wrap">
    <div class="brand">
      <span class="brand-mark"></span>
      <span class="brand-name">T.R. Kemble Inc.<br>/ Auctioneers</span>
    </div>
    <div class="tagline">North Carolina Auctions and Auctioneering</div>
    <div class="call">
      <span class="call-icon">
        <svg width="18" height="18" viewBox="0 0 24 24"><path fill="#fff" d="M6.6 10.8a15 15 0 0 0 6.6 6.6l2.2-2.2c.3-.3.7-.4 1-.2 1.1.4 2.3.6 3.6.6.6 0 1 .4 1 1V20c0 .6-.4 1-1 1A17 17 0 0 1 3 4c0-.6.4-1 1-1h3.5c.6 0 1 .4 1 1 0 1.3.2 2.5.6 3.6.1.3 0 .7-.2 1z"/></svg>
      </span>
      <div><small>CALL US :</small><strong>(555) 318-6402</strong></div>
    </div>
  </div>
</header>

<nav class="main-nav">
  <div class="wrap">
    <ul>
      <li class="n-home">HOME</li><li class="n-auc">AUCTIONS</li><li class="n-svc">AUCTION SERVICES</li><li class="n-sel">SELLERS</li><li class="n-live">TR KEMBLE LIVESTOCK</li><li class="n-about">ABOUT US</li><li class="n-contact">CONTACT US</li>
    </ul>
  </div>
</nav>

<section class="hero">
  <div class="slide-frame"><div class="slide-photo" role="img" aria-label="Autumn farmland with bare trees reflected in a pond"></div></div>
  <div class="slide-caption">
    <h2>NORTH CAROLINA AUCTIONS AND<br>AUCTIONEERING</h2>
    <p>Our auction business was started in 1979.</p>
  </div>
  <div class="slide-arrows"><span>&#8249;</span><span>&#8250;</span></div>
</section>

<section class="welcome">
  <h1>WELCOME TO TR KEMBLE</h1>
  <p>Our auction business was started in 1979. We conduct farm equipment, logging &amp; industrial equipment, real estate, antique &amp; cattle sales.<br>
  T. R. Kemble, owner/president, was raised on the family farm in Ashby County. This farm has been in his family since 1921. The office for the auction business is also located at this farm.</p>
</section>

<section class="featured">
  <div class="wrap">
    <div class="section-head"><h2>FEATURED AUCTIONS</h2><span class="pager">&#8249; &#8250;</span></div>
    <div class="auction-list">
      <div class="auction-card"><div class="auction-thumb t1" role="img" aria-label="Old tractor in a field at sunset"></div><h3>COMPLETE DISPERSAL</h3><p>LIVE ON-SITE AUCTION</p></div>
      <div class="auction-card"><div class="auction-thumb t2" role="img" aria-label="Black cattle on green pasture"></div><h3>COMPLETE DISPERSAL</h3><p>LIVE ON-SITE AUCTION</p></div>
      <div class="auction-card"><div class="auction-thumb t3" role="img" aria-label="Green farm tractor on grass"></div><h3>COMPLETE DISPERSAL</h3><p>LIVE ON-SITE AUCTION</p></div>
      <div class="auction-card"><div class="auction-thumb t4" role="img" aria-label="Combine harvesting a wheat field"></div><h3>COMPLETE DISPERSAL</h3><p>LIVE ON-SITE AUCTION</p></div>
    </div>
  </div>
</section>

<section class="news">
  <div class="wrap">
    <div class="section-head"><h2>NEWS &amp; EVENTS</h2><span class="pager-box"><span>&#8249;</span><span>&#8250;</span></span></div>
    <div class="news-list">
      <article class="news-item">
        <div class="news-thumb n1" role="img" aria-label="Country house lit at dusk"></div>
        <div><h3>IT IS A LONG ESTABLISHED FACT</h3><em>Posted on 27 March 2014</em><p>It is a long established fact that a reader will be<br>distracted by the readable content of a page when<br>looking at its layout...</p></div>
      </article>
      <article class="news-item">
        <div class="news-thumb n2" role="img" aria-label="Figure silhouetted against a golden sunset"></div>
        <div><h3>IT IS A LONG ESTABLISHED FACT</h3><em>Posted on 27 March 2014</em><p>It is a long established fact that a reader will be<br>distracted by the readable content of a page when<br>looking at its layout...</p></div>
      </article>
    </div>
  </div>
</section>

<footer class="site-footer">
  <div class="wrap footer-cols">
    <div class="footer-brand"><span class="brand-mark"></span><span class="brand-name">T.R. Kemble Inc.<br>/ Auctioneers</span></div>
    <div class="signup">
      <h4>EMAIL SIGNUP</h4>
      <p>Get our recent updates through your email id</p>
      <div class="field">Enter your email id :</div>
      <span class="btn">SUBSCRIBE NOW</span>
    </div>
    <div class="contact">
      <h4>CONTACT INFO</h4>
      <div class="co">T. R. KEMBLE INC. / AUCTIONEERS</div>
      <div>4710 NC Hwy 91, Cedar Bend, NC 27999</div>
      <div>Phone : (555) 318-6402 6:15 AM - 9:59 PM</div>
      <div>Mobile : (555) 274-8813 trkemble@trkemble-example.com</div>
      <div>Email : sales@trk-example.com, office@trk-example.com</div>
    </div>
    <div class="follow">
      <h4>FOLLOW US :</h4>
      <ul>
        <li><span class="dot"></span>: Friendbook</li>
        <li><span class="dot"></span>: Chirper</li>
        <li><span class="dot"></span>LinkPro</li>
      </ul>
    </div>
  </div>
</footer>

<div class="bottom-bar">
  <div class="wrap">
    <div class="foot-nav">Home<span>|</span>Auctions<span>|</span>Auction Services<span>|</span>Sellers<span>|</span>TR Kemble Livestock<span>|</span>About Us<span>|</span>Contact Us</div>
    <div class="copy">Copyright © 2014. T.R. Kemble, Inc. / Auctioneers. All rights reserved.</div>
    <div class="badges"><i class="b1"></i><i class="b2"></i><i class="b3"></i></div>
  </div>
</div>

</body>
</html>
```